World travel poster - I want to remember where I've been!

I would like a poster for me to print and keep in my home as a record of my world travels. It must look like a mechanical sign in an airport (see picture for example) However I am flexible with exact layout, if you'd like to add images used to enhance poster etc. I have also uploaded some pictures from my travels if you would like to use some or all of them. They are named according to location.

Poster must include:
USA 2003
Malaysia 2006
Thailand 2007
Italy 2009
India, Vietnam, Hong Kong 2010
Bali 2011
Malaysia 2012
Singapore 2012
Vietnam, Cambodia, Laos 2013
Europe 2015

and the quote:

"The world is a book and those who do not travel read only one page."
― Severin of Caldra
Updates

Hi there. I have uploaded some photos of my travels to possibly use in my poster. They are named according to location. I haven't decided if I prefer the originial layout or with images, so please post both for me to consider. Thanks so much for your time to consider my project.

Target Market(s)

Something to catch the eye of visitors and remind me of my adventures.
A classic piece that is a conversation starter.

Industry/Entity Type

Airport

Font styles to use
Other font styles liked:
• Airport mechanical font

Requirements
Must have
• Some lettering like a mechanical airport board (see image attached for example).
Dimensions that are easy to print - either A3, or a long/narrow poster.
Nice to have
• A splash of colour or an image, maybe the words 'arrivals' or 'departures'

Use of some of my pictures if it doesn't look too busy.
Should not have
• Anything too over the top.

```html
<!DOCTYPE html>
<html lang="en">
<head>
<meta charset="utf-8">
<title>Departures – Travel Record Poster</title>
<link rel="stylesheet" href="https://fonts.googleapis.com/css2?family=Montserrat:wght@300;700&family=Oswald:wght@500&display=swap">
<style>
  :root {
    --bg: #2c2c2c;
    --bg-light: #363636;
    --flap-top: #3d3d3d;
    --flap-bottom: #2a2a2a;
    --flap-edge: #1a1a1a;
    --split: #111;
    --letter: #f2f2f2;
    --digit: #f3e3a4;
    --accent: #f5d417;
    --quote: #e6e6e6;
    --credit: #cfcfcf;
  }
  * { box-sizing: border-box; margin: 0; padding: 0; }
  html, body { width: 837px; height: 1200px; overflow: hidden; }
  body {
    background: radial-gradient(ellipse at 50% 40%, var(--bg-light), var(--bg) 70%);
    position: relative;
    font-family: "Montserrat", sans-serif;
  }
  .heading {
    position: absolute; left: 34px; top: 30px;
    display: flex; align-items: center; gap: 34px;
  }
  .heading__icon { width: 62px; height: 34px; }
  .heading__title {
    font-weight: 700; font-size: 34px; letter-spacing: 4px;
    color: var(--accent); line-height: 1;
  }
  .board {
    position: absolute; left: 34px; top: 121px;
    display: flex; flex-direction: column; gap: 16px;
  }
  .row { display: flex; align-items: center; gap: 5px; height: 52px; }
  .flap {
    position: relative; width: 40px; height: 52px;
    background: linear-gradient(var(--flap-top) 0 50%, var(--flap-bottom) 50% 100%);
    border: 1px solid var(--flap-edge); border-radius: 3px;
    box-shadow: 0 2px 3px rgba(0,0,0,.5);
    font-family: "Oswald", sans-serif; font-weight: 500;
    font-size: 36px; line-height: 50px; text-align: center;
    color: var(--letter);
  }
  .flap::after {
    content: ""; position: absolute; left: 0; right: 0; top: 50%;
    height: 2px; margin-top: -1px; background: var(--split);
  }
  .flap--digit, .flap--mark { color: var(--digit); }
  .flag {
    position: relative; width: 84px; height: 50px; margin-left: 8px;
    box-shadow: 0 2px 3px rgba(0,0,0,.5);
  }
  .flag + .flag { margin-left: 9px; }
  .flag svg { display: block; width: 84px; height: 50px; }
  .flag::after {
    content: ""; position: absolute; left: 0; right: 0; top: 50%;
    height: 2px; margin-top: -1px; background: rgba(0,0,0,.55);
  }
  .quote {
    position: absolute; left: 34px; top: 950px;
    font-weight: 300; font-size: 44px; line-height: 56px; color: var(--quote);
  }
  .quote__highlight { display: block; font-weight: 700; color: var(--accent); }
  .quote__credit {
    display: block; margin-top: 10px;
    font-weight: 300; font-size: 19px; line-height: 24px; color: var(--credit);
  }
</style>
</head>
<body>
<svg width="0" height="0" style="position:absolute" aria-hidden="true">
  <defs>
    <polygon id="star" points="0,-1 0.2245,-0.309 0.951,-0.309 0.363,0.118 0.588,0.809 0,0.382 -0.588,0.809 -0.363,0.118 -0.951,-0.309 -0.2245,-0.309"/>
  </defs>
</svg>

<header class="heading">
  <svg class="heading__icon" viewBox="0 0 62 34" aria-hidden="true">
    <path fill="#f5d417" d="M2 17 Q2 13 8 13 L24 13 L14 1 L21 1 L38 13 L54 13 Q62 14 62 17 Q62 20 54 21 L38 21 L21 33 L14 33 L24 21 L8 21 Q2 21 2 17 Z M2 17 L0 8 L5 8 L10 13 Z"/>
  </svg>
  <h1 class="heading__title">DEPARTURES</h1>
</header>

<main class="board">
  <div class="row">
    <span class="flap">U</span><span class="flap">S</span><span class="flap">A</span><span class="flap flap--mark">-</span><span class="flap flap--digit">2</span><span class="flap flap--digit">0</span><span class="flap flap--digit">0</span><span class="flap flap--digit">3</span>
    <span class="flag"><svg viewBox="0 0 84 50" role="img" aria-label="Flag of the United States">
      <rect width="84" height="50" fill="#b22234"/>
      <g fill="#fff"><rect y="3.85" width="84" height="3.85"/><rect y="11.54" width="84" height="3.85"/><rect y="19.23" width="84" height="3.85"/><rect y="26.92" width="84" height="3.85"/><rect y="34.62" width="84" height="3.85"/><rect y="42.31" width="84" height="3.85"/></g>
      <rect width="34" height="27" fill="#3c3b6e"/>
    </svg></span>
  </div>

  <div class="row">
    <span class="flap">M</span><span class="flap">A</span><span class="flap">L</span><span class="flap">A</span><span class="flap">Y</span><span class="flap">S</span><span class="flap">I</span><span class="flap">A</span><span class="flap flap--mark">-</span><span class="flap flap--digit">2</span><span class="flap flap--digit">0</span><span class="flap flap--digit">0</span><span class="flap flap--digit">6</span>
    <span class="flag"><svg viewBox="0 0 84 50" role="img" aria-label="Flag of Malaysia">
      <rect width="84" height="50" fill="#cc0001"/>
      <g fill="#fff"><rect y="3.57" width="84" height="3.57"/><rect y="10.71" width="84" height="3.57"/><rect y="17.86" width="84" height="3.57"/><rect y="25" width="84" height="3.57"/><rect y="32.14" width="84" height="3.57"/><rect y="39.29" width="84" height="3.57"/><rect y="46.43" width="84" height="3.57"/></g>
      <rect width="42" height="28.6" fill="#010066"/>
      <circle cx="17" cy="14.3" r="9" fill="#fc0"/><circle cx="20" cy="14.3" r="7.6" fill="#010066"/>
      <use href="#star" transform="translate(30 14.3) scale(6)" fill="#fc0"/>
    </svg></span>
  </div>

  <div class="row">
    <span class="flap">T</span><span class="flap">H</span><span class="flap">A</span><span class="flap">I</span><span class="flap">L</span><span class="flap">A</span><span class="flap">N</span><span class="flap">D</span><span class="flap flap--mark">-</span><span class="flap flap--digit">2</span><span class="flap flap--digit">0</span><span class="flap flap--digit">0</span><span class="flap flap--digit">7</span>
    <span class="flag"><svg viewBox="0 0 84 50" role="img" aria-label="Flag of Thailand">
      <rect width="84" height="50" fill="#a51931"/>
      <rect y="8.33" width="84" height="33.34" fill="#f4f5f8"/>
      <rect y="16.67" width="84" height="16.66" fill="#2d2a4a"/>
    </svg></span>
  </div>

  <div class="row">
    <span class="flap">I</span><span class="flap">T</span><span class="flap">A</span><span class="flap">L</span><span class="flap">Y</span><span class="flap flap--mark">-</span><span class="flap flap--digit">2</span><span class="flap flap--digit">0</span><span class="flap flap--digit">0</span><span class="flap flap--digit">9</span>
    <span class="flag"><svg viewBox="0 0 84 50" role="img" aria-label="Flag of Italy">
      <rect width="28" height="50" fill="#009246"/><rect x="28" width="28" height="50" fill="#fff"/><rect x="56" width="28" height="50" fill="#ce2b37"/>
    </svg></span>
  </div>

  <div class="row">
    <span class="flap">I</span><span class="flap">N</span><span class="flap">D</span><span class="flap">I</span><span class="flap">A</span><span class="flap flap--mark">,</span><span class="flap">V</span><span class="flap">I</span><span class="flap">E</span><span class="flap">T</span><span class="flap">N</span><span class="flap">A</span><span class="flap">M</span>
    <span class="flag"><svg viewBox="0 0 84 50" role="img" aria-label="Flag of India">
      <rect width="84" height="16.67" fill="#ff9933"/><rect y="16.67" width="84" height="16.66" fill="#fff"/><rect y="33.33" width="84" height="16.67" fill="#138808"/>
      <circle cx="42" cy="25" r="6" fill="none" stroke="#000080" stroke-width="1.4"/>
    </svg></span>
    <span class="flag"><svg viewBox="0 0 84 50" role="img" aria-label="Flag of Vietnam">
      <rect width="84" height="50" fill="#da251d"/>
      <use href="#star" transform="translate(42 26) scale(15)" fill="#ff0"/>
    </svg></span>
  </div>

  <div class="row">
    <span class="flap flap--mark">&amp;</span><span class="flap">H</span><span class="flap">O</span><span class="flap">N</span><span class="flap">G</span><span class="flap">K</span><span class="flap">O</span><span class="flap">N</span><span class="flap">G</span><span class="flap flap--digit">2</span><span class="flap flap--digit">0</span><span class="flap flap--digit">1</span><span class="flap flap--digit">0</span>
    <span class="flag"><svg viewBox="0 0 84 50" role="img" aria-label="Flag of Hong Kong, red field with white flower emblem">
      <rect width="84" height="50" fill="#de2910"/>
    </svg></span>
  </div>

  <div class="row">
    <span class="flap">B</span><span class="flap">A</span><span class="flap">L</span><span class="flap">I</span><span class="flap flap--mark">-</span><span class="flap flap--digit">2</span><span class="flap flap--digit">0</span><span class="flap flap--digit">1</span><span class="flap flap--digit">3</span>
    <span class="flag"><svg viewBox="0 0 84 50" role="img" aria-label="Flag of Bali, orange field with provincial emblem">
      <rect width="84" height="50" fill="#f29a0c"/>
    </svg></span>
  </div>

  <div class="row">
    <span class="flap">M</span><span class="flap">A</span><span class="flap">L</span><span class="flap">A</span><span class="flap">Y</span><span class="flap">S</span><span class="flap">I</span><span class="flap">A</span><span class="flap flap--mark">-</span><span class="flap flap--digit">2</span><span class="flap flap--digit">0</span><span class="flap flap--digit">1</span><span class="flap flap--digit">2</span>
    <span class="flag"><svg viewBox="0 0 84 50" role="img" aria-label="Flag of Malaysia">
      <rect width="84" height="50" fill="#cc0001"/>
      <g fill="#fff"><rect y="3.57" width="84" height="3.57"/><rect y="10.71" width="84" height="3.57"/><rect y="17.86" width="84" height="3.57"/><rect y="25" width="84" height="3.57"/><rect y="32.14" width="84" height="3.57"/><rect y="39.29" width="84" height="3.57"/><rect y="46.43" width="84" height="3.57"/></g>
      <rect width="42" height="28.6" fill="#010066"/>
      <circle cx="17" cy="14.3" r="9" fill="#fc0"/><circle cx="20" cy="14.3" r="7.6" fill="#010066"/>
      <use href="#star" transform="translate(30 14.3) scale(6)" fill="#fc0"/>
    </svg></span>
  </div>

  <div class="row">
    <span class="flap">S</span><span class="flap">I</span><span class="flap">N</span><span class="flap">G</span><span class="flap">A</span><span class="flap">P</span><span class="flap">O</span><span class="flap">R</span><span class="flap">E</span><span class="flap flap--digit">2</span><span class="flap flap--digit">0</span><span class="flap flap--digit">1</span><span class="flap flap--digit">2</span>
    <span class="flag"><svg viewBox="0 0 84 50" role="img" aria-label="Flag of Singapore">
      <rect width="84" height="25" fill="#ef3340"/><rect y="25" width="84" height="25" fill="#fff"/>
      <circle cx="15" cy="12.5" r="7.5" fill="#fff"/><circle cx="18.5" cy="12.5" r="7" fill="#ef3340"/>
      <g fill="#fff">
        <use href="#star" transform="translate(23 7.5) scale(1.6)"/>
        <use href="#star" transform="translate(18.5 10.5) scale(1.6)"/>
        <use href="#star" transform="translate(27.5 10.5) scale(1.6)"/>
        <use href="#star" transform="translate(20 15.5) scale(1.6)"/>
        <use href="#star" transform="translate(26 15.5) scale(1.6)"/>
      </g>
    </svg></span>
  </div>

  <div class="row">
    <span class="flap">V</span><span class="flap">I</span><span class="flap">E</span><span class="flap">T</span><span class="flap">N</span><span class="flap">A</span><span class="flap">M</span><span class="flap flap--mark">,</span><span class="flap">L</span><span class="flap">A</span><span class="flap">O</span><span class="flap">S</span><span class="flap flap--mark">&amp;</span>
    <span class="flag"><svg viewBox="0 0 84 50" role="img" aria-label="Flag of Vietnam">
      <rect width="84" height="50" fill="#da251d"/>
      <use href="#star" transform="translate(42 26) scale(15)" fill="#ff0"/>
    </svg></span>
    <span class="flag"><svg viewBox="0 0 84 50" role="img" aria-label="Flag of Laos">
      <rect width="84" height="50" fill="#ce1126"/><rect y="12.5" width="84" height="25" fill="#002868"/>
      <circle cx="42" cy="25" r="10" fill="#fff"/>
    </svg></span>
  </div>

  <div class="row">
    <span class="flap">C</span><span class="flap">A</span><span class="flap">M</span><span class="flap">B</span><span class="flap">O</span><span class="flap">D</span><span class="flap">I</span><span class="flap">A</span><span class="flap flap--mark">-</span><span class="flap flap--digit">2</span><span class="flap flap--digit">0</span><span class="flap flap--digit">1</span><span class="flap flap--digit">3</span>
    <span class="flag"><svg viewBox="0 0 84 50" role="img" aria-label="Flag of Cambodia with white temple emblem">
      <rect width="84" height="50" fill="#032ea1"/><rect y="12.5" width="84" height="25" fill="#e00025"/>
    </svg></span>
  </div>

  <div class="row">
    <span class="flap">E</span><span class="flap">U</span><span class="flap">R</span><span class="flap">O</span><span class="flap">P</span><span class="flap">E</span><span class="flap flap--mark">-</span><span class="flap flap--digit">2</span><span class="flap flap--digit">0</span><span class="flap flap--digit">1</span><span class="flap flap--digit">5</span>
    <span class="flag"><svg viewBox="0 0 84 50" role="img" aria-label="Flag of Europe">
      <rect width="84" height="50" fill="#1d3b8f"/>
      <g fill="#fc0">
        <use href="#star" transform="translate(42 13) scale(2)"/>
        <use href="#star" transform="translate(48 14.6) scale(2)"/>
        <use href="#star" transform="translate(52.4 19) scale(2)"/>
        <use href="#star" transform="translate(54 25) scale(2)"/>
        <use href="#star" transform="translate(52.4 31) scale(2)"/>
        <use href="#star" transform="translate(48 35.4) scale(2)"/>
        <use href="#star" transform="translate(42 37) scale(2)"/>
        <use href="#star" transform="translate(36 35.4) scale(2)"/>
        <use href="#star" transform="translate(31.6 31) scale(2)"/>
        <use href="#star" transform="translate(30 25) scale(2)"/>
        <use href="#star" transform="translate(31.6 19) scale(2)"/>
        <use href="#star" transform="translate(36 14.6) scale(2)"/>
      </g>
    </svg></span>
  </div>
</main>

<blockquote class="quote">
  The world is a book and<br>
  those who do not travel read
  <strong class="quote__highlight">only one page.</strong>
  <cite class="quote__credit">- Severin of Caldra</cite>
</blockquote>
</body>
</html>
```